Meadowlight Soaps Business Card

The new business card design will incorporate my new logo components designed by one of your designers. Meadowlight Soaps creates high quality soaps and bath products. They would be suited for a Spa, Bed and Breakfast, Boutique environment. The look should be a white background.
Classy, soft and using the colour palet of the logo. The card will be two sided.

Reason: Need more time to make some changes and decide.

Target Market(s)

Looking to appeal to an upper end market. Spas, boutiques, independent gift stores, bridal salons, bed and breakfast, etc. I want the card to impart a sense of elegance, tranquility and Meadowlight. But also quality and value.

Industry/Entity Type

Business

Font styles to use
Sans Serif
Script

Requirements
Must have
• My logo on the front. But also on the back but faded out to allow written notes on the back.
On the front : Carol Pritchett
Owner/Creator
48 Fenwick Rd
Guelph, Ont N4K 2P9
519.402.6183
Creating Quality Handcrafted Soaps And Bath Products
Custom and Wholesale Orders Welcome
Www.meadowlightsoaps.ca
Www.facebook.com / MeadowlightSoapandBath
info@meadowlightsoaps.ca

```html
<!DOCTYPE html>
<html lang="en">
<head>
<meta charset="utf-8">
<title>Meadowlight Soaps Business Card</title>
<link rel="stylesheet" href="https://fonts.googleapis.com/css2?family=Lato:wght@400;700&family=Italianno&display=swap">
<style>
  :root {
    --backdrop: #4a4a4a;
    --paper: #ffffff;
    --sage: #88b2a6;
    --sage-faint: #e4eeeb;
    --swoosh: #c4c4c4;
    --ink-soft: #a9a9a9;
    --ink-muted: #b9b9b9;
    --blush-faint: #f6ece6;
  }
  * { box-sizing: border-box; margin: 0; padding: 0; }
  html, body {
    width: 1200px; height: 1000px; overflow: hidden;
    background: var(--backdrop);
  }
  .canvas { position: relative; width: 1200px; height: 1000px; }
  .card {
    position: absolute; width: 566px; height: 331px;
    background: var(--paper); overflow: hidden;
    font-family: 'Lato', sans-serif;
  }
  .card--front { left: 99px; top: 129px; }
  .card--back { left: 485px; top: 544px; }

  /* Front */
  .brand {
    position: absolute; left: 20px; top: 150px; width: 260px;
    text-align: center;
  }
  .brand__dot {
    display: block; width: 64px; height: 64px; margin: 0 auto 14px;
    border-radius: 50%; background: var(--sage-faint);
  }
  .brand__name {
    font-family: 'Lato', sans-serif; font-weight: 400;
    font-size: 26px; letter-spacing: 1px; color: var(--sage);
    line-height: 1.2;
  }
  .contact { position: absolute; left: 340px; top: 36px; }
  .contact__name {
    font-family: 'Italianno', cursive; font-size: 38px;
    color: var(--sage); line-height: 1; letter-spacing: 1px;
  }
  .contact__role {
    font-size: 15px; color: var(--ink-soft); margin-top: 2px;
  }
  .contact__address {
    font-size: 13px; font-weight: 700; color: var(--ink-soft);
    line-height: 20px; margin-top: 10px; font-style: normal;
  }
  .contact__list { list-style: none; margin-top: 12px; }
  .contact__item {
    display: flex; align-items: center; gap: 6px;
    font-size: 13px; font-weight: 700; color: var(--ink-soft);
    height: 21.5px;
  }
  .contact__icon { width: 15px; height: 15px; flex: none; }
  .wave { position: absolute; left: 0; bottom: 0; }

  /* Back */
  .notes__label {
    position: absolute; left: 30px; top: 34px;
    font-family: 'Italianno', cursive; font-size: 36px;
    color: var(--sage); line-height: 1;
  }
  .faded-brand {
    position: absolute; left: 150px; top: 40px; width: 270px;
    text-align: center;
  }
  .faded-brand__dot {
    display: block; width: 150px; height: 150px; margin: 0 auto 14px;
    border-radius: 50%; background: var(--blush-faint); opacity: .7;
  }
  .faded-brand__name {
    font-size: 26px; font-weight: 400; letter-spacing: 1px;
    color: var(--sage-faint);
  }
  .tagline {
    position: absolute; left: 0; right: 0; top: 259px;
    text-align: center; font-size: 15px; font-weight: 700;
    color: var(--ink-muted); line-height: 22px;
  }
</style>
</head>
<body>
<main class="canvas">

  <section class="card card--front" aria-label="Business card front">
    <div class="brand">
      <span class="brand__dot"></span>
      <p class="brand__name">Meadowlight Soaps</p>
    </div>

    <div class="contact">
      <h1 class="contact__name">Carol Pritchett</h1>
      <p class="contact__role">Owner</p>
      <address class="contact__address">48 Fenwick Rd<br>Guelph,Ont N4K 2P9</address>
      <ul class="contact__list">
        <li class="contact__item">
          <svg class="contact__icon" viewBox="0 0 16 16" aria-hidden="true">
            <path d="M4 1.5c1 0 1.6 2.6 1.4 3.2-.3.8-1.3 1-1 2 .6 1.8 2 3.3 3.8 4 .9.3 1.2-.7 2-1 .6-.2 3.3.4 3.3 1.4 0 1.2-1.2 2.6-2.6 2.6C6 13.7 2.3 10 2 4.2 2 2.7 3 1.5 4 1.5z" fill="var(--sage)"/>
          </svg>
          519.402.6183
        </li>
        <li class="contact__item">
          <svg class="contact__icon" viewBox="0 0 16 16" aria-hidden="true">
            <rect x="1" y="3.5" width="14" height="9" fill="var(--sage)"/>
            <path d="M1.5 4l6.5 5 6.5-5" fill="none" stroke="#fff" stroke-width="1.2"/>
          </svg>
          info@meadowlightsoaps.ca
        </li>
        <li class="contact__item">
          <svg class="contact__icon" viewBox="0 0 16 16" aria-hidden="true">
            <circle cx="8" cy="8" r="6.5" fill="none" stroke="var(--sage)" stroke-width="1.6"/>
            <path d="M1.5 8h13M8 1.5c-3 3.5-3 9.5 0 13M8 1.5c3 3.5 3 9.5 0 13" fill="none" stroke="var(--sage)" stroke-width="1.2"/>
          </svg>
          www.meadowlightsoaps.ca
        </li>
        <li class="contact__item">
          <svg class="contact__icon" viewBox="0 0 16 16" aria-hidden="true">
            <circle cx="8" cy="8" r="5" fill="var(--sage)"/>
          </svg>
          MeadowlightSoapandBath
        </li>
      </ul>
    </div>

    <svg class="wave" width="566" height="331" viewBox="0 0 566 331" aria-hidden="true">
      <path d="M0 276 C150 330 260 335 360 290 C430 258 500 240 566 240 L566 256 C500 256 430 275 360 305 C270 345 150 335 0 286 Z" fill="var(--swoosh)"/>
      <path d="M0 296 C120 330 250 345 360 306 C440 276 500 264 566 264 L566 331 L0 331 Z" fill="var(--sage)"/>
    </svg>
  </section>

  <section class="card card--back" aria-label="Business card back">
    <div class="faded-brand" aria-hidden="true">
      <span class="faded-brand__dot"></span>
      <p class="faded-brand__name">Meadowlight Soaps</p>
    </div>
    <p class="notes__label">Notes:</p>
    <p class="tagline">Creating Quality Handcrafted Soaps And Bath Products<br>Custom and Wholesale Orders Welcome</p>
  </section>

</main>
</body>
</html>
```